I want a website to be designed for our new company, it's an import and export company for variety of things.

please see the attached Logo for our company and the Images for our different sections for our busienss

Target Market(s)

multiple

Coding

Coded - Design and coding required

Number of Pages Required

5+ page

Font styles to use
Sans Serif

Colors

Designer to choose colors to be used in the design.

Requirements
Must have
• KVR GLOBALINKS
• KVR globalinks Trading & Contracting provides various services. The Company offers infrastructure construction, oil, enegy and gas services, agricultural projects, real estate development, travel and tourism, and food processing and trading.
• Civil contracting for infrastructure, residential and heavy projects. Through its main subsidiaries; distribution of general food products, construction chemicals including corrosion inhibitors and electrical machinery; provides catering and travel agency services; ownership and operation of a school; offers human sources services including manpower supply.
• Drilling and Gold Mines Used Machinery, All Kinds of Construction Machinery, Drilling Machines are manufactured and sold.
Nice to have
• good designa and beautiful colours, it has too look professional

```html
<!DOCTYPE html>
<html lang="en">
<head>
<meta charset="utf-8">
<title>KVR Globalinks — Website Concepts</title>
<link rel="stylesheet" href="https://fonts.googleapis.com/css2?family=Cinzel:wght@400;600&family=Roboto:wght@400;500;700&family=Roboto+Slab:wght@400;700&display=swap">
<style>
:root{
  --board:#e6e6e6;
  --ink:#161616;
  --ink-2:#1e1e1e;
  --ink-3:#0c0c0c;
  --white:#ffffff;
  --paper:#f4f4f4;
  --orange:#f6a22b;
  --red:#e8141b;
  --muted:#8a8a8a;
  --text:#555555;
  --serif:'Cinzel', serif;
  --sans:'Roboto', sans-serif;
  --slab:'Roboto Slab', serif;
}
*{box-sizing:border-box;margin:0;padding:0}
html,body{width:846px;height:1200px;overflow:hidden}
body{background:var(--board);position:relative;font-family:var(--sans);color:var(--text)}
.abs{position:absolute}
.site{position:absolute;width:288px;background:var(--white);overflow:hidden;box-shadow:0 1px 4px rgba(0,0,0,.12)}
.site--light{left:89px;top:73px;height:1096px}
.site--dark{left:444px;top:73px;height:778px;background:var(--ink)}
section,header,footer{position:relative;width:100%}
p{font-size:3.6px;line-height:8px}
.photo{position:absolute}

/* ---------- light concept ---------- */
.topbar{height:10.5px;background:#000;color:#fff;font-size:3.3px;display:flex;align-items:center;padding:0 21px;gap:8px}
.topbar .login{margin-left:auto}
.mainnav{height:19px;background:#fff;font-family:var(--serif);font-size:3.8px;color:#333;display:flex;align-items:center;padding:0 21px}
.mainnav span{margin-right:8px}
.mainnav .active{color:var(--orange)}
.mainnav .right{margin-left:auto;display:flex}
.mainnav .right span{margin:0 0 0 10px}
.brand-disc{position:absolute;left:121px;top:14px;width:47px;height:47px;border-radius:50%;background:#111;border:1.5px solid #333;display:flex;align-items:center;justify-content:center;text-align:center;z-index:3;color:#fff;font-family:var(--serif);font-size:4px;line-height:5px}
.hero-l{height:140px}
.hero-l .title{left:21px;top:41px;font-family:var(--serif);font-size:12.5px;color:#fff;font-weight:400}
.hero-l p{position:absolute;left:21px;top:58px;color:#fff;width:140px;line-height:7px}
.btn-orange{position:absolute;background:var(--orange);color:#fff;font-family:var(--serif);display:flex;align-items:center;justify-content:center}
.search{height:35px;background:var(--ink)}
.field{position:absolute;top:7px;height:15px;border:1px solid #bbb;color:#fff;font-size:3.6px;display:flex;align-items:center;padding:0 2px}
.field i{margin-left:auto;font-style:normal}
.cap{position:absolute;top:25px;font-size:3px;color:#ccc}
.about{height:122px;background:var(--paper)}
.about h3{position:absolute;left:21px;top:13px;font-family:var(--serif);font-weight:400;font-size:7.5px;color:#222}
.about h2{position:absolute;left:21px;top:22px;font-family:var(--serif);font-weight:400;font-size:10.5px;color:#222}
.about p{position:absolute;left:21px;top:36px;width:120px;text-align:justify}
.services-intro{height:67px;background:#fff;text-align:center}
.services-intro h2{position:absolute;top:19px;width:100%;font-family:var(--serif);font-weight:400;font-size:9px;color:#222}
.services-intro p{position:absolute;left:35px;top:35px;width:218px}
.split{height:104px;background:var(--ink)}
.split h2{position:absolute;font-family:var(--serif);font-weight:400;font-size:8px;color:#fff}
.split h4{position:absolute;font-size:4.2px;color:#fff;font-weight:500}
.split p{position:absolute;color:#ddd;width:103px}
.btn-outline{position:absolute;border:0.8px solid var(--orange);color:#fff;font-family:var(--serif);font-size:4.2px;display:flex;align-items:center;justify-content:center}
.icon-disc{position:absolute;width:16px;height:16px;border-radius:50%;background:#fff;border:1px solid #ccc;display:flex;align-items:center;justify-content:center;z-index:2}
.offer-l{height:154px;background:#fff}
.offer-l h2{position:absolute;top:20px;width:100%;text-align:center;font-family:var(--serif);font-weight:400;font-size:9.5px;color:#222}
.card-l{position:absolute;top:45px;width:58px;height:65px;border:0.8px solid #d6d6d6;text-align:center;background:#fff}
.card-l.hover{border-color:var(--orange)}
.card-l svg{margin-top:3px}
.card-l h5{font-family:var(--serif);font-weight:400;font-size:4.3px;line-height:6px;color:#222;margin-top:1px}
.card-l p{font-size:3px;line-height:5.6px;padding:1px 3px;text-align:justify}
.go{position:absolute;left:22px;bottom:-6px;width:13px;height:13px;border-radius:50%;background:var(--orange);color:#fff;font-size:6px;display:flex;align-items:center;justify-content:center}
.dots{position:absolute;width:100%;display:flex;justify-content:center;gap:3px}
.dots b{width:3px;height:3px;border-radius:50%;background:#111}
.dots b.off{background:transparent;border:.6px solid #111}
.dots.light b{background:#fff}
.dots.light b.off{background:transparent;border-color:#fff}
.testimonials{height:137px;background:linear-gradient(180deg,#55585c,#6b6e72 50%,#4e5156)}
.testimonials h2{position:absolute;top:9px;width:100%;text-align:center;font-family:var(--serif);font-weight:400;font-size:10px;color:#fff}
.testimonials>p{position:absolute;left:55px;top:22px;width:178px;text-align:center;color:#fff;line-height:7px;font-size:3.8px}
.quote{position:absolute;top:42px;width:68px;height:76px;background:#fff;padding:4px 3px}
.quote p{font-size:3px;line-height:6.8px;color:#333;text-align:justify}
.quote h6{font-family:var(--serif);font-weight:400;font-size:4px;color:#222;margin-top:3px}
.quote em{position:absolute;font-style:normal;color:#ccc;font-size:5px}
.contact-l{height:203px;background:linear-gradient(180deg,#fff 0,#fff 112px,var(--ink) 112px)}
.touch-box{position:absolute;left:30px;top:22px;width:229px;height:117px;background:#fff}
.touch-box h2{position:absolute;left:4px;top:9px;font-family:var(--serif);font-weight:400;font-size:8.5px;color:#222}
.inp{position:absolute;left:4px;width:83px;height:9px;background:#fff;border:.5px solid #eee;font-size:2.8px;padding:2px 3px;color:#666}
.footer-links{position:absolute;top:184px;width:100%;display:flex;justify-content:center;gap:8px;font-family:var(--serif);font-size:3.6px;color:#fff}
.copy-l{position:absolute;top:192px;width:100%;text-align:center;font-family:var(--serif);font-size:3.4px;color:#fff}
.foot-brand{position:absolute;top:152px;width:100%;text-align:center;font-family:var(--serif);font-size:5px;color:#fff;display:flex;justify-content:center;align-items:center;gap:3px}
.foot-brand i{width:5px;height:5px;border-radius:50%;background:#fff;display:inline-block}

/* ---------- dark concept ---------- */
.header-d{height:29px;background:var(--ink)}
.brand-d{position:absolute;left:22px;top:10px;display:flex;align-items:center;gap:3px;font-family:var(--slab);font-size:4.6px;color:#fff}
.brand-d i{width:6px;height:6px;border-radius:50%;border:.7px solid #fff;display:block}
.social{position:absolute;top:7px;display:flex;gap:2.5px;left:190px}
.social i{width:7px;height:7px;border-radius:50%;border:.6px solid #fff;display:block}
.callus{position:absolute;left:224px;top:5px;display:flex;gap:3px;color:#fff;align-items:center}
.callus .ring{width:9px;height:9px;border-radius:50%;border:.6px solid #fff;display:flex;align-items:center;justify-content:center}
.callus small{display:block;font-size:3.2px}
.callus b{display:block;font-size:4px}
.nav-d{position:absolute;left:97px;top:19px;display:flex;gap:12px;font-size:3.6px;color:#fff}
.nav-d .active{color:var(--red)}
.hero-d{height:140px}
.hero-d h1{position:absolute;top:44px;width:100%;text-align:center;font-family:var(--slab);font-weight:700;font-size:13px;color:#fff}
.hero-d p{position:absolute;top:62px;left:60px;width:168px;text-align:center;color:#fff;line-height:6.5px;font-size:3.9px}
.btn-red{position:absolute;background:var(--red);color:#fff;font-family:var(--slab);font-weight:700;display:flex;align-items:center;justify-content:center}
.welcome{height:93px;background:var(--ink-2)}
.welcome h2{position:absolute;top:10px;width:100%;text-align:center;font-family:var(--slab);font-weight:700;font-size:10.5px;color:#fff;word-spacing:2px}
.welcome p{position:absolute;left:30px;top:27px;width:228px;text-align:center;color:#ddd;line-height:8.6px;font-size:3.7px}
.services-d{height:113px;background:linear-gradient(120deg,#1b1b1b,#262626 50%,#141414)}
.services-d h2{position:absolute;left:22px;top:22px;font-family:var(--slab);font-weight:700;font-size:9.5px;color:#fff}
.services-d>p{position:absolute;left:22px;top:38px;width:107px;color:#ddd;line-height:8.7px;font-size:3.8px}
.svc{position:absolute;top:24px;width:59px;height:67px;background:#fff;border-radius:1.5px;text-align:center}
.svc svg{margin-top:7px}
.svc h5{font-family:var(--sans);font-weight:500;font-size:5px;color:#222;margin-top:2px}
.svc p{font-size:2.8px;line-height:5.8px;padding:1px 4px;color:#777}
.offer-d{height:109px;background:#1c1c1c}
.offer-d h2,.projects h2{position:absolute;top:12px;width:100%;text-align:center;font-family:var(--slab);font-weight:700;font-size:9.5px;color:#fff}
.tile{position:absolute;top:33px;width:75px;height:53px}
.tile span{position:absolute;bottom:3px;width:100%;text-align:center;font-family:var(--slab);font-weight:700;font-size:4.6px;color:#fff}
.projects{height:170px;background:var(--ink-3)}
.proj{position:absolute;width:79px;height:54px}
.proj-hover{position:absolute;inset:0;background:rgba(20,30,40,.45);display:flex;align-items:center;justify-content:center}
.proj-hover i{width:12px;height:12px;border-radius:50%;border:.7px solid #fff;display:block}
.footer-d{height:124px;background:linear-gradient(180deg,#161616,#202020)}
.footer-d h4{position:absolute;top:31px;font-family:var(--slab);font-weight:700;font-size:5.2px;color:#fff}
.contact-row{position:absolute;left:22px;display:flex;gap:4px;font-size:3.5px;line-height:5.4px;color:#ddd}
.contact-row svg{flex:none;margin-top:.5px}
.quick{position:absolute;left:102px;top:41px;font-size:3.5px;line-height:8.4px;color:#ddd}
.quote-note{position:absolute;left:164px;top:43px;font-size:3.2px;color:#ddd}
.qin{position:absolute;width:50px;height:10px;border:.6px solid #888;font-size:2.6px;color:#ccc;padding:3px 3px}
.copy-d{position:absolute;top:114px;width:100%;text-align:center;font-family:var(--slab);font-size:3.6px;color:#ddd}
.rule{position:absolute;left:0;right:0;top:107px;height:.5px;background:#333}
</style>
</head>
<body>

<!-- ================= Light concept ================= -->
<main class="site site--light">
  <div class="topbar">
    <span>⌂ English ⌄</span><span>✆ +555 0100 2200</span><span>✉ info@kvrglobalinks.com</span>
    <span class="login">🔒 Log In (Or) Register</span>
  </div>
  <nav class="mainnav">
    <span class="active">Home</span><span>About Us</span><span>Import And Export</span>
    <div class="right"><span>Serivces</span><span>Products</span><span>Contact Us</span></div>
  </nav>
  <div class="brand-disc">KVR<br>GLOBALINKS</div>

  <section class="hero-l">
    <div class="photo" role="img" aria-label="Global logistics montage with world map, handshake and trucks" style="inset:0;background:linear-gradient(120deg,#1f2a44 0%,#3b4a66 40%,#56637a 70%,#2c3549 100%)"></div>
    <h1 class="abs title">KVR Globalinks.</h1>
    <p>Lorem ipsum dolor sit amet, consectetur adipiscing elit, sed do eiusmod tempor incididunt ut labore et dolore magna aliqua.</p>
    <div class="btn-orange" style="left:21px;top:76px;width:56px;height:19px;font-size:6.6px">Get Started</div>
  </section>

  <section class="search">
    <div class="field" style="left:21px;width:95px">Product description</div>
    <div class="field" style="left:119px;width:56px">Select<i>⌄</i></div>
    <div class="field" style="left:179px;width:56px">Import<i>⌄</i></div>
    <div class="field" style="left:248px;width:19px;justify-content:center">
      <svg width="6" height="6" viewBox="0 0 12 12"><circle cx="5" cy="5" r="3.6" fill="none" stroke="#fff" stroke-width="1.6"/><line x1="7.6" y1="7.6" x2="11" y2="11" stroke="#fff" stroke-width="1.8"/></svg>
    </div>
    <span class="cap" style="left:21px">Example - oil, enegy and gas services etc...</span>
    <span class="cap" style="left:119px">Country Import Export Data</span>
    <span class="cap" style="left:179px">Select Import or Export</span>
  </section>

  <section class="about">
    <h3>About Us</h3>
    <h2>KVR Globalinks.</h2>
    <p>Lorem ipsum dolor sit amet, consectetur adipiscing elit, sed do eiusmod tempor incididunt ut labore et dolore magna aliqua. Ut enim ad minim veniam, quis nostrud exercitation ullamco laboris nisi ut aliquip ex ea commodo consequat. Duis aute irure dolor in reprehenderit in voluptate velit esse cillum dolore eu fugiat nulla pariatur. Excepteur sint occaecat cupidatat non proident, sunt in culpa qui officia deserunt mollit anim id est laborum.</p>
    <div class="btn-orange" style="left:21px;top:100px;width:37px;height:11px;font-size:4px">Read More</div>
    <div class="photo" role="img" aria-label="Warehouse worker checking cardboard boxes" style="left:177px;top:14px;width:90px;height:99px;border:1.5px solid #fff;background:linear-gradient(135deg,#1f4f8e,#c9b08a 55%,#e7ddd0)"></div>
  </section>

  <section class="services-intro">
    <h2>Services</h2>
    <p>Lorem ipsum dolor sit amet, consectetur adipiscing elit, sed do eiusmod tempor incididunt ut labore et dolore magna aliqua. Ut enim ad minim veniam, quis nostrud exercitation ullamco laboris nisi ut aliquip ex ea commodo consequat.</p>
  </section>

  <section class="split">
    <h2 style="left:21px;top:15px">Trading</h2>
    <h4 style="left:21px;top:28px">Finibus Bonorum et Malorum</h4>
    <p style="left:21px;top:37px">Lorem ipsum dolor sit amet, consectetur adipiscing elit, sed do eiusmod tempor incididunt ut labore et dolore magna aliqua. Ut enim ad minim veniam, quis nostrud exercitation ullamco laboris nisi ut aliquip ex ea commodo consequat.</p>
    <div class="btn-outline" style="left:21px;top:76px;width:42px;height:13px">View More</div>
    <div class="photo" role="img" aria-label="Shipping container lifted at a port terminal" style="left:144px;top:0;width:144px;height:104px;background:linear-gradient(160deg,#e9eef3,#2f4f8c 45%,#c28b3a 85%)"></div>
    <div class="icon-disc" style="left:136px;top:45px">
      <svg width="9" height="9" viewBox="0 0 20 20" fill="none" stroke="#333" stroke-width="1.2"><rect x="2" y="5" width="12" height="9"/><circle cx="15" cy="13" r="3.5"/><line x1="5" y1="8" x2="11" y2="8"/></svg>
    </div>
  </section>

  <section class="split">
    <div class="photo" role="img" aria-label="Business handshake over a world map of global partners" style="left:0;top:0;width:144px;height:104px;background:linear-gradient(170deg,#8fb3cf,#c4b29a 55%,#6a5a4a)"></div>
    <div class="icon-disc" style="left:136px;top:45px">
      <svg width="9" height="9" viewBox="0 0 20 20" fill="none" stroke="#333" stroke-width="1.2"><rect x="4" y="2" width="11" height="15"/><line x1="7" y1="6" x2="12" y2="6"/><line x1="7" y1="9" x2="12" y2="9"/><path d="M7 13l2 2 4-4"/></svg>
    </div>
    <h2 style="left:164px;top:15px">Contracting</h2>
    <h4 style="left:164px;top:28px">Finibus Bonorum et Malorum</h4>
    <p style="left:164px;top:37px">Lorem ipsum dolor sit amet, consectetur adipiscing elit, sed do eiusmod tempor incididunt ut labore et dolore magna aliqua. Ut enim ad minim veniam, quis nostrud exercitation ullamco laboris nisi ut aliquip ex ea commodo consequat.</p>
    <div class="btn-outline" style="left:164px;top:76px;width:42px;height:13px">View More</div>
  </section>

  <section class="offer-l">
    <h2>What We Offer</h2>
    <div class="card-l" style="left:21.5px">
      <svg width="12" height="16" viewBox="0 0 12 16" fill="none" stroke="#333" stroke-width=".7"><rect x="2" y="5" width="8" height="10"/><line x1="6" y1="0" x2="6" y2="5"/><line x1="2" y1="2" x2="10" y2="2"/><rect x="4" y="8" width="4" height="3"/></svg>
      <h5>Infrastructure<br>Construction</h5>
      <p>Lorem ipsum dolor sit amet, consectetur adipiscing elit, sed do eiusmod tempor incididunt</p>
      <span class="go">›</span>
    </div>
    <div class="card-l" style="left:79.5px">
      <svg width="18" height="16" viewBox="0 0 18 16" fill="none" stroke="#333" stroke-width=".7"><rect x="2" y="5" width="6" height="9"/><rect x="10" y="5" width="6" height="9"/><path d="M2 5l3-3 3 3M10 5l3-3 3 3"/><line x1="1" y1="14.5" x2="17" y2="14.5"/></svg>
      <h5>Food<br>Processing</h5>
      <p>Lorem ipsum dolor sit amet, consectetur adipiscing elit, sed do eiusmod tempor incididunt</p>
      <span class="go">›</span>
    </div>
    <div class="card-l hover" style="left:141.5px">
      <svg width="18" height="16" viewBox="0 0 18 16" fill="none" stroke="#333" stroke-width=".7"><rect x="2" y="4" width="14" height="10"/><circle cx="12" cy="4" r="3"/><line x1="4" y1="8" x2="10" y2="8"/><line x1="4" y1="11" x2="12" y2="11"/></svg>
      <h5>Travel And<br>Tourism</h5>
      <p>Lorem ipsum dolor sit amet, consectetur adipiscing elit, sed do eiusmod tempor incididunt</p>
      <span class="go">›</span>
    </div>
    <div class="card-l" style="left:204px">
      <svg width="18" height="16" viewBox="0 0 18 16" fill="none" stroke="#333" stroke-width=".7"><circle cx="7" cy="3" r="2"/><path d="M7 5v5l-3 5M7 10l3 5M4 7h6"/><path d="M13 14V7M11 9l2-2 2 2"/></svg>
      <h5>Agricultural<br>Projects</h5>
      <p>Lorem ipsum dolor sit amet, consectetur adipiscing elit, sed do eiusmod tempor incididunt</p>
      <span class="go">›</span>
    </div>
    <div class="dots" style="top:128px"><b></b><b class="off"></b><b></b></div>
  </section>

  <section class="testimonials">
    <div class="photo" role="img" aria-label="Blurred supermarket aisle behind a faint world map" style="inset:0;background:linear-gradient(180deg,rgba(40,42,46,.35),rgba(90,70,60,.35))"></div>
    <h2>Testimonials</h2>
    <p>Lorem ipsum dolor sit amet, consectetur adipiscing elit, sed do eiusmod tempor incididunt ut labore et dolore magna aliqua.</p>
    <div class="quote" style="left:34.5px"><em style="left:3px;top:0">“</em><p>Lorem ipsum dolor sit amet, consectetur adipiscing elit, sed do eiusmod tempor incididunt ut labore et dolore magna a. Ut enim ad minim veniam, quis nostrud exercitation ullamco laboris nisi ut aliquip ex ea commodo consequat. Duis aute irure dolor.</p><h6>Daniel Hartwell</h6><em style="right:3px;bottom:0">”</em></div>
    <div class="quote" style="left:103px"><em style="left:3px;top:0">“</em><p>Lorem ipsum dolor sit amet, consectetur adipiscing elit, sed do eiusmod tempor incididunt ut labore et dolore magna a. Ut enim ad minim veniam, quis nostrud exercitation ullamco laboris nisi ut aliquip ex ea commodo consequat. Duis aute irure dolor.</p><h6>Sofia Brennan</h6><em style="right:3px;bottom:0">”</em></div>
    <div class="quote" style="left:172px"><em style="left:3px;top:0">“</em><p>Lorem ipsum dolor sit amet, consectetur adipiscing elit, sed do eiusmod tempor incididunt ut labore et dolore magna a. Ut enim ad minim veniam, quis nostrud exercitation ullamco laboris nisi ut aliquip ex ea commodo consequat. Duis aute irure dolor.</p><h6>Leo Marsh</h6><em style="right:3px;bottom:0">”</em></div>
    <div class="dots light" style="top:125px"><b></b><b class="off"></b><b></b></div>
  </section>

  <section class="contact-l">
    <div class="touch-box">
      <h2>Get In Touch</h2>
      <div class="inp" style="top:23px">Name</div>
      <div class="inp" style="top:36px">Email</div>
      <div class="inp" style="top:48px">Phone number</div>
      <div class="inp" style="top:61px;height:28px">Messages</div>
      <div class="btn-orange" style="left:5px;top:94px;width:82px;height:11px;font-size:4.2px">Submit</div>
      <svg class="abs" style="left:104px;top:0" width="125" height="117" viewBox="0 0 125 117">
        <polygon points="35,0 125,0 125,117 35,117 0,58" fill="var(--orange)"/>
        <polygon points="39,0 125,0 125,117 39,117 5,58" fill="#6f5a4a" role="img" aria-label="Logistics worker with clipboard beside stacked boxes"/>
      </svg>
    </div>
    <div class="foot-brand"><i></i>KVR GLOBALINKS</div>
    <div class="footer-links"><span>Home</span><span>About Us</span><span>Import And Export</span><span>Services</span><span>Products</span><span>Contact Us</span></div>
    <div class="copy-l">© Copyright 2020 KVR Globalinks. All rights reserved.</div>
  </section>
</main>

<!-- ================= Dark concept ================= -->
<main class="site site--dark">
  <header class="header-d">
    <div class="brand-d"><i></i>KVR GLOBALINKS</div>
    <div class="social"><i></i><i></i><i></i></div>
    <div class="callus">
      <span class="ring"><svg width="5" height="5" viewBox="0 0 10 10"><path d="M2 1l2 2-1 1.5c.8 1.4 1.7 2.3 3 3L7.5 6.5l2 2L8 10C4 9 1 6 0 2z" fill="#fff"/></svg></span>
      <span><small>Call us :</small><b>555 -0100- 2200</b></span>
    </div>
    <nav class="nav-d"><span class="active">Home</span><span>About Us</span><span>Import And Export</span><span>Services</span><span>Products</span><span>Contact Us</span></nav>
  </header>

  <section class="hero-d">
    <div class="photo" role="img" aria-label="Cargo port with plane, container stacks, cranes and ship" style="inset:0;background:linear-gradient(100deg,#6e8aa8 0%,#3f6b8a 25%,#9c5a3a 45%,#3d7fa8 70%,#8ab6d3 100%)"></div>
    <h1>KVR GLOBALINKS.</h1>
    <p>Lorem ipsum dolor sit amet, consectetur adipiscing elit, sed do eiusmod tempor incididunt ut labore et dolore magna aliqua.</p>
    <div class="btn-red" style="left:118px;top:78px;width:47px;height:13px;font-size:5.2px">GET STARTED</div>
    <svg class="abs" style="left:0;bottom:0" width="288" height="22" viewBox="0 0 288 22" preserveAspectRatio="none"><polygon points="0,22 0,12 30,8 60,14 90,6 120,13 145,0 170,10 200,5 230,12 260,7 288,11 288,22" fill="var(--ink-2)"/></svg>
  </section>

  <section class="welcome">
    <h2>WELCOME TO KVR GLOBALINKS</h2>
    <p>Lorem ipsum dolor sit amet, consectetur adipiscing elit, sed do eiusmod tempor incididunt ut labore et dolore magna aliqua. Ut enim ad minim veniam, quis nostrud exercitation ullamco laboris nisi ut aliquip ex ea commodo consequat. Duis aute irure dolor in reprehenderit in voluptate velit esse cillum dolore eu fugiat nulla pariatur. Excepteur sint occaecat cupidatat non proident, sunt in culpa qui officia deserunt mollit anim id est laborum</p>
    <div class="btn-red" style="left:127px;top:69px;width:33px;height:11px;font-size:3.6px">READ MORE</div>
  </section>

  <section class="services-d">
    <h2>SERVICES</h2>
    <p>Lorem ipsum dolor sit amet, consectetur adipiscing elit, sed do eiusmod tempor incididunt ut labore et dolore magna aliqua. Ut enim ad minim veniam, quis nostrud exercitation ullamco laboris nisi</p>
    <div class="btn-red" style="left:22px;top:80px;width:33px;height:10px;font-size:3.6px">VIEW MORE</div>
    <div class="svc" style="left:141.5px">
      <svg width="18" height="18" viewBox="0 0 20 20" fill="none" stroke="#222" stroke-width=".8"><rect x="2" y="6" width="11" height="9"/><path d="M5 6V4h5v2"/><circle cx="14" cy="14" r="4"/><path d="M10 14h8M14 10v8"/></svg>
      <h5>TRADING</h5>
      <p>Lorem ipsum dolor sit amet, consectetur adipiscing elit, sed do eiusmod tempor incididunt ut labore et dolore magna aliqua.</p>
    </div>
    <div class="svc" style="left:207px">
      <svg width="18" height="18" viewBox="0 0 20 20" fill="none" stroke="#222" stroke-width=".8"><rect x="3" y="2" width="11" height="16"/><path d="M5 5h7M5 8h7M5 11h4"/><circle cx="7" cy="15" r="1.5"/><path d="M17 4l-6 10"/></svg>
      <h5>CONTRACTING</h5>
      <p>Lorem ipsum dolor sit amet, consectetur adipiscing elit, sed do eiusmod tempor incididunt ut labore et dolore magna aliqua.</p>
    </div>
  </section>

  <section class="offer-d">
    <h2>WHAT WE OFFER</h2>
    <div class="tile photo" role="img" aria-label="Modern residential house at dusk" style="left:21.5px;background:linear-gradient(180deg,#7fa6c9,#8a6a4e 60%,#3e4a38)"><span>REAL ESTATE DEVELOPMENT</span></div>
    <div class="tile photo" role="img" aria-label="Travel map with sunglasses and passport" style="left:105px;background:linear-gradient(135deg,#c9b98a,#7ea9b6 50%,#a8432e)"><span>TRAVEL AND TOURISM</span></div>
    <div class="tile photo" role="img" aria-label="Food processing line with worker" style="left:190px;background:linear-gradient(135deg,#ddd6cc,#b65a50 55%,#3b3b3b)"><span>FOOD PROCESSING</span></div>
    <div class="dots light" style="top:93px"><b></b><b class="off"></b><b></b></div>
  </section>

  <section class="projects">
    <h2>OUR PROJECTS</h2>
    <div class="proj photo" role="img" aria-label="Aerial view of a large building complex" style="left:22px;top:31px;background:linear-gradient(135deg,#9aa49a,#c9ccc8 50%,#6d7a6e)"></div>
    <div class="proj photo" role="img" aria-label="Heavy drilling machinery in mist" style="left:105px;top:31px;background:linear-gradient(135deg,#4d5a61,#6f7d6a 50%,#2d3a3f)"><div class="proj-hover"><i></i></div></div>
    <div class="proj photo" role="img" aria-label="Offshore oil rig at sea" style="left:188px;top:31px;background:linear-gradient(135deg,#3d6e7a,#2c5764 55%,#8a5a3a)"></div>
    <div class="proj photo" role="img" aria-label="Assorted fresh groceries" style="left:22px;top:89px;background:linear-gradient(135deg,#f4f1ea,#d9612e 45%,#6f9a3a)"></div>
    <div class="proj photo" role="img" aria-label="Electric vehicle charging station" style="left:105px;top:89px;background:linear-gradient(135deg,#e4e6e8,#6b6f75 50%,#2f9b5a)"></div>
    <div class="proj photo" role="img" aria-label="Greenhouse with tablet showing crops" style="left:188px;top:89px;background:linear-gradient(135deg,#d7e0dc,#9fb3a2 55%,#5f7a5a)"></div>
    <div class="dots light" style="top:153px"><b class="off"></b><b></b><b class="off"></b></div>
  </section>

  <footer class="footer-d">
    <svg class="abs" style="left:0;top:-14px" width="288" height="26" viewBox="0 0 288 26" preserveAspectRatio="none"><polygon points="0,26 0,14 40,16 80,10 110,8 145,0 175,8 210,12 250,9 288,14 288,26" fill="#181818"/></svg>
    <h4 style="left:22px">CONTACT US</h4>
    <div class="contact-row" style="top:42px"><svg width="4" height="5" viewBox="0 0 8 10"><path d="M4 0a4 4 0 0 1 4 4c0 3-4 6-4 6S0 7 0 4a4 4 0 0 1 4-4z" fill="none" stroke="#ddd"/></svg><span>KVR Globalinks.<br>Harbor Point, 4410 Dock Road</span></div>
    <div class="contact-row" style="top:56px"><svg width="4" height="4" viewBox="0 0 10 10"><path d="M2 1l2 2-1 1.5c.8 1.4 1.7 2.3 3 3L7.5 6.5l2 2L8 10C4 9 1 6 0 2z" fill="#ddd"/></svg><span>Phone:555-0142-7700</span></div>
    <div class="contact-row" style="top:65px"><svg width="4" height="4" viewBox="0 0 10 10"><rect x="1" y="3" width="8" height="6" fill="none" stroke="#ddd"/><rect x="3" y="0.5" width="4" height="3" fill="none" stroke="#ddd"/></svg><span>Fax: 555-0142-7701</span></div>
    <div class="contact-row" style="top:74px"><svg width="4" height="4" viewBox="0 0 10 10"><rect x="0.5" y="2" width="9" height="6" fill="none" stroke="#ddd"/><path d="M.5 2l4.5 3.5L9.5 2" fill="none" stroke="#ddd"/></svg><span>Email:<br>info@kvrglobalinks.com</span></div>
    <h4 style="left:102px">QUICK LINKS</h4>
    <div class="quick">Home<br>About Us<br>Import And Export<br>Services<br>Products<br>Contact Us</div>
    <h4 style="left:164px">REQUEST A QUOTE</h4>
    <div class="quote-note">Alternatively You Can Fill In The Following Contact Form:</div>
    <div class="qin" style="left:164px;top:54px">Name</div>
    <div class="qin" style="left:216px;top:54px">E - Mail</div>
    <div class="qin" style="left:164px;top:67px">Subject</div>
    <div class="qin" style="left:216px;top:67px">Message</div>
    <div class="btn-red" style="left:164px;top:83px;width:56px;height:10px;font-size:4px">SUBMIT</div>
    <div class="rule"></div>
    <div class="copy-d">(c) 2020 KVR Globalinks | All Rights Reserved | Terms and Conditions</div>
  </footer>
</main>

</body>
</html>
```